Yoga/movement guide/teacher for adult yoga practice and kid yoga

What is the positioning or mission statement of your company? to guide individuals in a yoga-based safe and sustainable movement practice applicable to all ages and body types. Currently my focus is working with children in daycare and school settings, but my goal is to expand into private yoga practice for adults, and potentially as part of rented space in studios. I hope to find a way to work with children AND adults (so would love for logo to be appealing to both), but current focus is with children based on need and demand in the community. yoga for children also compliments my backround as a pediatrician/neonatologist, and I greatly miss interacting with children. I also want to emphasize a yoga/movement practice that is focused more on what one feels internally through movement. NOT what one looks like asthetically. I believe in removing all mirrors from yoga/movement practice. It should be an experience of movement/poses/yoga through appropriate cueing and education. It is not about the details of how far the knee should bend, or how high the leg should be. Focusing on foudation first, core, then core engagement and ultimately expression of poses/movements. A focus on strength, stability and mobility, not just flexibility, which is the common perception/association with yoga. I also want individuals to learn to be an advocate of their own health. Through guidance, I hope for individuals to connect with their body so they know themselves so well to be able to advocate for themselves in the modern healthcare world. This internal experience and connection is so essential in a world where modern medicine has become a business and it is all about making a dollar. the connection with patients is lost, and individuals need to learn to empower themselves and through their new found voice to be able to articulate what is wrong.<br/>Does your company have a tagline or slogan that should be included with the logo? "Move Gently, Glow Within"<br/>What do you hope your company can be known for? Accessible yoga for a sustained practice. A guided movement practice where one gains information and knowledge of oneself through a mind/body connection. For one feel good physically with a new awaraness of their internal radiance that exists in all beings. Physical rejuvenation egnites a light and increases energy to flow through the physical body, which ultimately tranlates into works of kindness for others and out in the world. <br/>What color palettes might you prefer? why? love the colors currently chosen<br/>Where will the logo be primarily used? initially business cards, but hopefully future websites, t-shirts, and potentially local magazine adds. Also starting with a small couple of banners for community events in the area. I currently practice as a nomad out of my car :)<br/>Are there any elements you would prefer to see in the logo? Movement. A modern depiction of a human body/figure practicing movement. Hoping to avoid a stereotypical yoga pose per say, just because I want to people to think of it more of a movement practice with yoga roots. Modern yoga. There are elements of breathing and connecting with oneself through the flow of breath and movement, but I do not focus on the meditative/cerebral aspect of the yoga practice. What I teach is almost reaching a meditative state through movement. I personally don't practice, nor resonate with just seated meditation. just not my thing :)<br/>In your opinion, what defines a well-designed logo? curiosity. enough info for individuals to think they know what it means, but want to know more. invokes curiosity, but not too abstract. Reproducible. not too complicated. I want also to invoke a community feel, so a design that appeals to all people within a community. <br/>What is your preference in reference to icons, typography, spokespeople (characters), etc.? modern design. I love the idea of a logo for my purposes, to invoke a sense of movement from within. So not too static. <br/>What words or icons must be included in the logo? movement with yoga roots. <br/>What logos do you like and why? A representation, but not exact. I think some ambiguity is intriguing for others, and also memorable. I want it to be an artistic representation of movement/yoga<br/>What logos do you dislike and why? too busy, too loud. <br/>In your opinion, what is the primary purpose for a logo? association<br/>Who is the primary target audience? (who is most likely to use your services/product?) Children and their parents, but ultimately to expand into teaching adults. I even have aspirations of prenatal and post-natal yoga. Potentially incorporating infants. <br/>Who currently uses your product the most? n/a (working in schools/daycare currently. It is currently all volunteer)<br/>Are you pleased with the range of people your company serves? n/a<br/>Are you looking to expand, modify, or completely change your target audience? or will it remain the same? yes! expand into an adult audience. <br/>How do you plan to focus on your target audience? currently by working through schools and daycares. hopefully ultimately through after school care programs and then offering kid yoga in an existing yoga studio (working on this with Q Studio in Ridgeland, currently)<br/>What are your main forms of advertising? word of mouth, schools, daycares. Happy kids talking to their parents about the yoga class they took and happy teachers :)<br/>How do most customers find out about your company?<br/>Which gender are you targeting? All genders! However, with kid yoga, often the maternal individual in the child's life is more involved with decision making as far as extracurricular activities

Target Market(s)

individuals and families interested in wellness and feeling great

Contact Information for Business Card

Dana Whitford
Yoga Instructor
RYT-200, RCYT

certified yoga teacher for adults and children

Colors

Designer to choose colors to be used in the design.

Requirements
Must have
• "Move Gently, Glow Within"
Nice to have
• logo with same colors

```html
<!DOCTYPE html>
<html lang="en">
<head>
<meta charset="utf-8">
<title>Glowfield Studios – Business Card</title>
<link rel="stylesheet" href="https://fonts.googleapis.com/css2?family=Arimo:wght@700&family=Lato:wght@400&display=swap">
<style>
  :root {
    --backdrop: #6f6f6f;
    --card-light: #ffffff;
    --card-dark: #262626;
    --name-yellow: #f5cf2a;
    --ink: #1e1e1e;
    --brand-grey: #6d6d6d;
    --brand-grey-light: #b9b9b9;
    --teal: #5bc8d2;
    --icon-white: #ffffff;
  }
  * { box-sizing: border-box; margin: 0; padding: 0; }
  html, body {
    width: 1200px; height: 900px; overflow: hidden;
    background: var(--backdrop);
    font-family: "Lato", sans-serif;
  }
  .canvas { position: relative; width: 1200px; height: 900px; }

  .card { position: absolute; top: 200px; width: 311px; height: 503px; }
  .card--front {
    left: 253px; background: var(--card-light);
    border-radius: 62px 0 62px 0;
  }
  .card--back {
    left: 627px; background: var(--card-dark);
    border-radius: 0 62px 0 62px;
  }

  .brand {
    position: absolute; left: 66px; width: 200px;
    font-family: "Lato", sans-serif; font-weight: 400;
    font-size: 36px; line-height: 40px; color: var(--brand-grey);
  }
  .card--front .brand { top: 120px; }
  .card--back .brand { top: 186px; color: var(--brand-grey-light); }

  .brand__tagline {
    position: absolute; left: 66px; font-size: 8px;
    letter-spacing: 1.3px; text-transform: uppercase; color: var(--teal);
    white-space: nowrap;
  }
  .card--front .brand__tagline { top: 210px; }
  .card--back .brand__tagline { top: 276px; }

  .contact { position: absolute; left: 34px; top: 309px; color: var(--ink); }
  .contact__name {
    font-family: "Arimo", sans-serif; font-weight: 700;
    font-size: 18px; line-height: 20px; color: var(--name-yellow);
  }
  .contact__role { font-size: 15px; line-height: 18px; }
  .contact__lines { list-style: none; margin-top: 12px; }
  .contact__line {
    display: flex; align-items: center; gap: 4px;
    font-size: 15px; line-height: 19px;
  }
  .contact__icon { width: 13px; height: 13px; flex: none; }
  .contact__address { margin-top: 12px; font-size: 15px; line-height: 18px; }

  .social {
    position: absolute; left: 100px; top: 435px;
    display: flex; gap: 4px; list-style: none;
  }
  .social__item {
    width: 24px; height: 24px; border-radius: 50%;
    border: 1.5px solid var(--icon-white);
  }
</style>
</head>
<body>
<main class="canvas">

  <section class="card card--front" aria-label="Card front">
    <p class="brand">Glowfield Studios</p>
    <p class="brand__tagline">Move Gently, Glow Within</p>

    <div class="contact">
      <h1 class="contact__name">DANA WHITFORD</h1>
      <p class="contact__role">Yoga Instructor</p>
      <ul class="contact__lines">
        <li class="contact__line">
          <svg class="contact__icon" viewBox="0 0 16 16" aria-hidden="true"><path fill="var(--name-yellow)" d="M1 5c0-2 3-3 7-3s7 1 7 3v2h-4V5.5H5V7H1zM3 8h10l1 6H2zm5 1.5a2 2 0 100 4 2 2 0 000-4z"/></svg>
          044-555 010 234
        </li>
        <li class="contact__line">
          <svg class="contact__icon" viewBox="0 0 16 16" aria-hidden="true"><rect x="1" y="3" width="14" height="10" fill="var(--name-yellow)"/><path d="M1.5 3.5L8 9l6.5-5.5" fill="none" stroke="#fff" stroke-width="1.2"/></svg>
          hello@glowfieldyoga.com
        </li>
        <li class="contact__line">
          <svg class="contact__icon" viewBox="0 0 16 16" aria-hidden="true"><circle cx="8" cy="8" r="7" fill="var(--name-yellow)"/><path d="M1 8h14M8 1c-3 3-3 11 0 14M8 1c3 3 3 11 0 14" fill="none" stroke="#fff" stroke-width="1"/></svg>
          www.glowfieldyoga.com
        </li>
      </ul>
      <p class="contact__address">18 Willow Lane<br>Ridgeland, 39157</p>
    </div>
  </section>

  <section class="card card--back" aria-label="Card back">
    <p class="brand">Glowfield Studios</p>
    <p class="brand__tagline">Move Gently, Glow Within</p>

    <ul class="social" aria-label="Social profiles">
      <li class="social__item"></li>
      <li class="social__item"></li>
      <li class="social__item"></li>
      <li class="social__item"></li>
    </ul>
  </section>

</main>
</body>
</html>
```